Business card design for holistic health care clinic

We need a double-sided business card design for our holistic health care clinic that integrates our logo design and also its color scheme. My business is called Valmira. It is an integrative medicine clinic. You have already done the logo for me. Please ensure an elegant and upscale design that is not cluttered, but still has all the necessary information (please see below for details).

Target Market(s)

Wellness, fitness, rehabilitation for educated, well-traveled open-minded clients who are focused on natural, organic, balanced and preventive healthcare and lifestyle.

Industry/Entity Type

Medical

Contact Information for Business Card

Modern, clean.

Number of Pages Required

1 page

Font styles to use
Serif
Sans Serif

Colors

Designer to choose colors to be used in the design.

Requirements
Must have
• Logo on one side, all other information on the other side.
• Other information should include:
• Tobias Wrenfeld - DOE, CPT, LMT
• 4100 East Marrow Drive
• Austin, TX 78119
• 512 555 0148
• 818 555 0192
• info@ValmiraHealth.example
• t.wrenfeld@ValmiraHealth.example
Nice to have
• Darker background on front - but not totally black - shaded/dark gray.

```html
<!DOCTYPE html>
<html lang="en">
<head>
<meta charset="utf-8">
<title>Valmira – Business Card</title>
<link rel="stylesheet" href="https://fonts.googleapis.com/css2?family=Source+Sans+3:ital,wght@0,400;0,600;0,700;1,400&display=swap">
<style>
  :root {
    --backdrop: #3a322e;
    --card: #1b1b1d;
    --card-edge: #26262a;
    --brand-blue: #1e90d2;
    --silver: #b9b9bc;
    --ink-light: #e6e6e6;
    --muted: #9a9a9e;
    --divider: #5a5a60;
  }
  * { box-sizing: border-box; margin: 0; padding: 0; }
  html, body {
    width: 1200px; height: 864px; overflow: hidden;
    background: var(--backdrop);
    font-family: "Source Sans 3", sans-serif;
  }
  .stage {
    position: relative; width: 1200px; height: 864px;
    display: flex; align-items: center; justify-content: center; gap: 40px;
  }
  .card {
    position: relative; width: 540px; height: 309px;
    background: linear-gradient(160deg, var(--card-edge), var(--card));
    border-radius: 3px;
    box-shadow: 0 14px 30px rgba(0,0,0,.45);
    overflow: hidden;
  }
  /* Front */
  .card-front { display: flex; flex-direction: column; align-items: center; justify-content: center; }
  .front-tagline {
    position: absolute; top: 34px; left: 0; right: 0; text-align: center;
    font-style: italic; font-size: 14px; color: var(--muted); letter-spacing: .3px;
  }
  .front-name {
    font-weight: 700; font-size: 84px; color: var(--silver);
    letter-spacing: 2px; text-transform: uppercase;
  }
  /* Back */
  .card-back { display: flex; align-items: center; padding: 0 30px 0 34px; }
  .brand-block { width: 232px; display: flex; flex-direction: column; }
  .brand-name {
    font-weight: 700; font-size: 50px; line-height: 1; color: var(--brand-blue);
    text-transform: uppercase; letter-spacing: 1px;
  }
  .brand-descriptor { margin-top: 6px; font-size: 15px; color: var(--brand-blue); font-weight: 600; }
  .divider { width: 1px; height: 150px; background: var(--divider); margin: 0 20px 0 12px; }
  .contact-block { flex: 1; color: var(--ink-light); font-size: 14.5px; line-height: 1.3; }
  .person-name { color: var(--brand-blue); font-weight: 700; font-size: 17px; text-transform: uppercase; margin-bottom: 6px; white-space: nowrap; }
  .person-credentials { font-size: 10.5px; font-weight: 600; text-transform: none; }
  .address { margin-bottom: 4px; }
  .contact-line { display: flex; align-items: center; gap: 8px; white-space: nowrap; }
  .contact-line svg { width: 12px; height: 12px; flex: none; fill: var(--brand-blue); }
  .contact-line.plain { padding-left: 20px; }
</style>
</head>
<body>
<main class="stage">
  <section class="card card-front" aria-label="Card front">
    <p class="front-tagline">helping the body help itself</p>
    <p class="front-name">Valmira</p>
  </section>

  <section class="card card-back" aria-label="Card back">
    <div class="brand-block">
      <p class="brand-name">Valmira</p>
      <p class="brand-descriptor">Integrative Holistic Medicine</p>
    </div>
    <div class="divider"></div>
    <div class="contact-block">
      <p class="person-name">Tobias Wrenfeld <span class="person-credentials">- DOE, CPT, LMT</span></p>
      <p class="address">4100 East Marrow Drive<br>Austin, TX 78119</p>
      <p class="contact-line">
        <svg viewBox="0 0 24 24" aria-hidden="true"><path d="M6.6 10.8a15.2 15.2 0 0 0 6.6 6.6l2.2-2.2a1 1 0 0 1 1-.25 11.4 11.4 0 0 0 3.6.57 1 1 0 0 1 1 1V20a1 1 0 0 1-1 1A17 17 0 0 1 3 4a1 1 0 0 1 1-1h3.5a1 1 0 0 1 1 1c0 1.25.2 2.45.57 3.57a1 1 0 0 1-.25 1z"/></svg>
        512 555 0148
      </p>
      <p class="contact-line">
        <svg viewBox="0 0 24 24" aria-hidden="true"><path d="M7 1h10a2 2 0 0 1 2 2v18a2 2 0 0 1-2 2H7a2 2 0 0 1-2-2V3a2 2 0 0 1 2-2zm0 3v15h10V4z"/></svg>
        818 555 0192
      </p>
      <p class="contact-line">
        <svg viewBox="0 0 24 24" aria-hidden="true"><path d="M2 5h20v14H2zm2 2v.4l8 5 8-5V7zm0 2.8V17h16V9.8l-8 5z"/></svg>
        t.wrenfeld@ValmiraHealth.example
      </p>
      <p class="contact-line">
        <svg viewBox="0 0 24 24" aria-hidden="true"><path d="M12 2a10 10 0 1 0 0 20 10 10 0 0 0 0-20zm0 2a8 8 0 0 1 6.9 4H15a12 12 0 0 0-1.5-3.9A8 8 0 0 1 12 4zM4.6 15h3.6a14 14 0 0 0 1.5 4.6A8 8 0 0 1 4.6 15zm0-6a8 8 0 0 1 5.1-4.6A14 14 0 0 0 8.2 9zm5.6 6h3.6a11 11 0 0 1-1.8 4.4A11 11 0 0 1 10.2 15zm0-6A11 11 0 0 1 12 4.6 11 11 0 0 1 13.8 9zm4.1 10.6a14 14 0 0 0 1.5-4.6h3.6a8 8 0 0 1-5.1 4.6z"/></svg>
        www.ValmiraHealth.example
      </p>
    </div>
  </section>
</main>
</body>
</html>
```